Brochure Redesign

We need a new, adapted, design for our Brochure. A few weeks ago we've setup a new Homepage design and for now we want to adapt our old Brochure to the new design.

Requirements:
-) Place the 3 products quite prominent
-) Place also our add ons
-) Use the Keyvisuals you can find on the Homepage

New Homepage: www.rufkontor-werk.at
Old Folder version - see attached

Requirements
Must have
• Logo and basic design from Homepage

```html
<!DOCTYPE html>
<html lang="de">
<head>
<meta charset="utf-8">
<title>Rufkontor – Folder</title>
<link href="https://fonts.googleapis.com/css2?family=Arimo:wght@400;700&family=Roboto+Condensed:wght@400;700&display=swap" rel="stylesheet">
<style>
:root{
  --wine:#7b1419;
  --wine-dark:#5e0d12;
  --orange:#f39322;
  --orange-deep:#e9781c;
  --yellow:#fcd41a;
  --yellow-soft:#fde27a;
  --tag:#fcd55a;
  --grey-card:#e6e6e8;
  --text:#3a3a3a;
  --muted:#5a5a5a;
  --white:#ffffff;
}
*{box-sizing:border-box;margin:0;padding:0}
html,body{width:1200px;height:961px;overflow:hidden;background:var(--white)}
body{position:relative;font-family:"Arimo",Arial,sans-serif;color:var(--text)}
.abs{position:absolute}
.crop-marks{position:absolute;inset:0}

/* left panel */
.benefits-bg{left:96px;top:124px;width:336px;height:300px}
.benefits{left:140px;top:190px;width:280px;color:var(--wine)}
.benefits h1{font-size:24px;font-weight:700;line-height:1}
.benefits h2{font-size:16.5px;font-weight:700;margin-top:5px}
.benefits ul{list-style:none;margin-top:18px;font-size:12.5px;line-height:15.5px}

.step{left:126px;width:282px;height:98px}
.step-photo{position:absolute;left:-2px;top:-44px;width:72px;height:72px;border-radius:50%;border:3px solid var(--white);box-shadow:0 1px 4px rgba(0,0,0,.25)}
.step-label{position:absolute;right:0;top:0;width:138px;height:17px;background:linear-gradient(90deg,var(--yellow-soft),var(--yellow));border-radius:9px 0 0 0;font-size:11px;font-weight:700;color:var(--wine);padding:2px 0 0 40px}
.step-body{position:absolute;left:30px;right:0;top:17px;height:66px;background:var(--grey-card);font-size:8.6px;line-height:11px;color:var(--muted);padding:6px 10px 0 24px}
.step-num{position:absolute;left:0;top:20px;width:34px;height:64px;background:var(--wine);border-radius:0 0 0 18px;color:var(--white);font-size:25px;font-weight:700;padding:18px 0 0 8px}
.step-num::before{content:"";position:absolute;left:0;top:-8px;width:34px;height:10px;background:var(--wine);border-radius:10px 0 0 0}

/* middle panel */
.trial-bg{left:432px;top:124px;width:336px;height:362px}
.app-bubble{left:478px;top:134px;width:160px;height:124px}
.app-text{left:504px;top:176px;width:120px;color:var(--wine)}
.app-text h3{font-size:14px;font-weight:700}
.app-text p{font-size:8.6px;line-height:10.5px;color:var(--wine-dark);margin-top:3px}
.store-badge{left:480px;top:280px;width:97px;height:34px;background:#111;border:1px solid #bbb;border-radius:5px}
.platform-badge{left:593px;top:272px;width:36px;height:46px;background:#8dbf3a;border-radius:10px 10px 6px 6px}
.phone{left:652px;top:214px;width:82px;height:110px;border-radius:12px;background:linear-gradient(160deg,#4a4a4a,#1f1f1f)}
.trial{left:464px;top:348px;width:260px;color:var(--white)}
.trial h3{font-size:16.5px;font-weight:700}
.trial p{font-size:10.2px;line-height:12.6px;margin-top:8px}

.contact-head{left:464px;top:504px}
.contact-head h2{font-size:21px;font-weight:700;color:var(--wine)}
.contact-head p{font-family:"Roboto Condensed",Arial,sans-serif;font-size:16.5px;color:#333;margin-top:3px}
.contact-role{left:470px;top:592px;width:124px;text-align:right;font-family:"Roboto Condensed",Arial,sans-serif}
.contact-role .role{font-size:12.5px;line-height:16px;color:var(--orange)}
.contact-role .name{font-size:10.5px;color:var(--muted);margin-top:6px}
.signature{left:540px;top:654px;width:56px;height:42px;background:linear-gradient(90deg,#e8e8e8,#f4f4f4);border-radius:4px}
.contact-lines{left:464px;top:728px;z-index:2;font-size:9.4px;line-height:11.5px;color:#444;display:grid;grid-template-columns:46px auto;white-space:nowrap}
.contact-photo{left:636px;top:558px;width:124px;height:288px;background:linear-gradient(180deg,#f0d9a8 0%,#e8c9a6 30%,#2b2b2f 52%,#1d1d21 100%);border-radius:56px 56px 0 0}

/* right panel */
.addons-head{left:768px;top:124px;width:336px;height:44px;background:var(--wine);color:var(--white);font-size:19px;font-weight:700;text-align:center;padding-top:12px}
.addon{left:790px;width:292px;text-align:center}
.addon-icon{width:80px;height:80px;border-radius:50%;margin:0 auto;background:radial-gradient(circle,#f7f7f7,#dcdcdc);box-shadow:0 1px 3px rgba(0,0,0,.2)}
.price{display:inline-block;background:var(--tag);border:1px solid #e8b52a;border-radius:6px;color:var(--wine);font-weight:700;font-size:13.5px;padding:3px 6px}
.addon h4{font-size:14.5px;color:var(--wine);margin-top:7px}
.addon p{font-size:9.3px;line-height:11px;color:var(--muted);margin-top:3px}
.price-row{display:flex;justify-content:center;gap:5px;margin-top:6px}
.price-col{display:flex;flex-direction:column;align-items:center;gap:4px}
.price-col span{font-size:9px;font-weight:700;color:var(--wine)}
</style>
</head>
<body>

<svg class="crop-marks" width="1200" height="961" aria-hidden="true" stroke="#999" stroke-width="1">
  <line x1="96" y1="96" x2="96" y2="114"/><line x1="68" y1="124" x2="86" y2="124"/>
  <line x1="432" y1="96" x2="432" y2="114"/><line x1="768" y1="96" x2="768" y2="114"/>
  <line x1="1104" y1="96" x2="1104" y2="114"/><line x1="1114" y1="124" x2="1132" y2="124"/>
  <line x1="96" y1="856" x2="96" y2="874"/><line x1="68" y1="846" x2="86" y2="846"/>
  <line x1="432" y1="856" x2="432" y2="874"/><line x1="768" y1="856" x2="768" y2="874"/>
  <line x1="1104" y1="856" x2="1104" y2="874"/><line x1="1114" y1="846" x2="1132" y2="846"/>
</svg>

<!-- left panel -->
<svg class="abs benefits-bg" viewBox="0 0 336 300" aria-hidden="true">
  <defs>
    <linearGradient id="benefitYellow" x1="0" x2="1">
      <stop offset="0" stop-color="#fde37e"/><stop offset=".6" stop-color="#fcd320"/><stop offset="1" stop-color="#eec016"/>
    </linearGradient>
  </defs>
  <path d="M0 0H336V190Q200 300 0 250Z" fill="#f39322"/>
  <path d="M0 0H336V150Q190 260 0 225Z" fill="url(#benefitYellow)"/>
</svg>
<div class="abs benefits">
  <h1>Ihre Vorteile</h1>
  <h2>Einfach, Immer, Erreichbar</h2>
  <ul>
    <li>- Individueller Meldetext</li>
    <li>- Beliebig viele Mitarbeiter</li>
    <li>- 24h Erreichbarkeit</li>
    <li>- Ohne Mindestvertragslaufzeit</li>
    <li>- Keine versteckten Callminuten</li>
  </ul>
</div>

<div class="abs step" style="top:414px">
  <div class="step-body">Das Service-Paket "Rund um die Uhr" steht Ihnen 24 Stunden am Tag, 365 Tage im Jahr zur Verfügung. Die Servicezeiten umfassen damit auch Sonn- und Feiertage.</div>
  <div class="step-label">Dateneingabe</div>
  <div class="step-num">1</div>
  <div class="step-photo" role="img" aria-label="Foto: Hände auf einer Tastatur" style="background:linear-gradient(135deg,#f3f3f3,#d9c3b0)"></div>
</div>
<div class="abs step" style="top:554px">
  <div class="step-body">Sofort nach erfolgreicher Buchung erhalten Sie Ihre Zielrufnummer. Leiten Sie Ihr Telefon einfach auf diese Nummer um (Hilfe).</div>
  <div class="step-label">Rufumleitung</div>
  <div class="step-num">2</div>
  <div class="step-photo" role="img" aria-label="Foto: Finger auf einer Telefontastatur" style="background:linear-gradient(135deg,#ececec,#c9b6a6)"></div>
</div>
<div class="abs step" style="top:696px">
  <div class="step-body">Ihr neues Sekretariat ist nun aktiv. Sie und all Ihre Mitarbeiter werden in Echtzeit, individuell über eingehende Anrufe informiert.</div>
  <div class="step-label">Ihr Sekretariat</div>
  <div class="step-num">3</div>
  <div class="step-photo" role="img" aria-label="Foto: Mitarbeiterin mit Headset" style="background:linear-gradient(135deg,#8a5a3c,#e9cdb4)"></div>
</div>

<!-- middle panel -->
<svg class="abs trial-bg" viewBox="0 0 336 362" aria-hidden="true">
  <defs>
    <linearGradient id="trialOrange" x1="0" x2="1">
      <stop offset="0" stop-color="#f6a236"/><stop offset="1" stop-color="#ef8520"/>
    </linearGradient>
  </defs>
  <path d="M0 362V90Q70 0 220 0H336V362Z" fill="url(#trialOrange)"/>
  <path d="M0 362V215Q30 95 190 72Q290 62 336 110V362Z" fill="#7b1419"/>
</svg>
<svg class="abs app-bubble" viewBox="0 0 160 124" aria-hidden="true">
  <defs>
    <linearGradient id="bubbleFill" x1="0" y1="0" x2="0" y2="1">
      <stop offset="0" stop-color="#fde39a"/><stop offset=".5" stop-color="#f9b94a"/><stop offset="1" stop-color="#f08a1e"/>
    </linearGradient>
  </defs>
  <path d="M6 4H150Q156 4 156 10L150 92Q150 98 144 98H120L130 120L98 98H16Q10 98 10 92L2 10Q2 4 6 4Z" fill="url(#bubbleFill)" stroke="#fff" stroke-width="3"/>
</svg>
<div class="abs app-text">
  <h3>Kostenlose App</h3>
  <p>Laden Sie jetzt die kostenlose telefonservice App direkt online herunter.</p>
</div>
<div class="abs store-badge" role="img" aria-label="Store-Badge"></div>
<div class="abs platform-badge" role="img" aria-label="Plattform-Badge"></div>
<div class="abs phone" role="img" aria-label="Abbildung: Smartphone mit geöffneter App"></div>
<div class="abs trial">
  <h3>24h - GRATIS -TEST</h3>
  <p>Wählen Sie Ihren persönlichen Meldetext und testen Sie uns 24 Stunden vollkommen kostenlos und unverbindlich.Wenn wir Sie überzeugt haben, können Sie in Ihrem Kundenbereich alle weiteren Daten ergänzen und Ihr neues Sekretariat fix buchen.</p>
</div>

<div class="abs contact-head">
  <h2>Ihr Ansprechpartner</h2>
  <p>Praxisnah. Kompetent. Engagiert.</p>
</div>
<div class="abs contact-role">
  <div class="role">Die RUFKONTOR Leitung<br>Marketing &amp; Sales</div>
  <div class="name">Frau Prok. Lena Hartmann</div>
</div>
<div class="abs signature" role="img" aria-label="Unterschrift"></div>
<div class="abs contact-photo" role="img" aria-label="Foto: Ansprechpartnerin im dunklen Blazer"></div>
<div class="abs contact-lines">
  <span>Freeline</span><span>08800 / 0800 41</span>
  <span>Email</span><span>info@rufkontor-werk.at</span>
  <span>Web</span><span>www.rufkontor-werk.at</span>
</div>

<!-- right panel -->
<div class="abs addons-head">ADD ON'S</div>

<div class="abs addon" style="top:186px">
  <div class="addon-icon" role="img" aria-label="Illustration: Bücherstapel mit Computermaus"></div>
  <div style="margin-top:12px"><span class="price">mtl. € 19,-</span></div>
  <h4>Online Wissensdatenbank</h4>
  <p>Bietet die Grundlage für die professionelle Sammlung<br>Ihrer Informationen. Strukturierte<br>Informationsaufbereitung ermöglicht Suchanfragen nach<br>Stichworten, Kategorien und/oder Freitext.<br>(Setup einmalig € 99,-)</p>
</div>

<div class="abs addon" style="top:404px">
  <div class="addon-icon" role="img" aria-label="Illustration: Kalenderblatt"></div>
  <div style="margin-top:12px"><span class="price">mtl. € 29,-</span></div>
  <h4>Online Terminkalender</h4>
  <p>Sämtliche Anforderungen wie Terminlängen, Kategorien,<br>Zeitfenster,etc. werden individuell an Ihre Bedürfnisse<br>angepasst und ermöglichen<br>ortsunabhängig alle Termine zu verwalten.<br>(Setup einmalig € 199,-)</p>
</div>

<div class="abs addon" style="top:622px">
  <div class="addon-icon" role="img" aria-label="Illustration: Mikrofon und Aufnahmegerät"></div>
  <div class="price-row">
    <div class="price-col"><span>Neutral</span><b class="price">mtl. € 4,90</b></div>
    <div class="price-col"><span>Personalisiert</span><b class="price">mtl. € 7,90</b></div>
    <div class="price-col"><span>Anrufbeantworter</span><b class="price">mtl. € 9,90</b></div>
  </div>
  <h4>Tonbänder &amp; Co</h4>
  <p>Sie haben die Möglichkeit mit neutralen und individuellen<br>Bandansagen oder einer Anrufbeantworterfunktion Ihren<br>Kunden noch mehr Service zu bieten.</p>
</div>

</body>
</html>
```